Breakthrough book for CEO's for navigating exponential change (very timely!)

This book changes the way leaders approach change. It comes from deep experience - seeing first hand what isn't working. It will be a book still being purchased in 5 or 10 years time, and broadly quoted. The author is female, doesn't want to shown up as "look at me" (the work is the hero) but needs to command authority among C-Suite which skews strongly male. The book is about systems thinking, hence why I've been exploring designs that cue "systems" (attached). It would be good to keep exploring this theme, along with others. Attached are files which give more background: including author / brand guidelines, a design brief, Bring your creativity and energy - and help me connect and cut through to the people who really need this book!

Target Market(s)

CEO's, Senior Executive Leaders

Industry/Entity Type

Business, Corporate

Font styles to use
Other font styles liked:
• See the brief: Raleway and Beyond Infinity

Colors

Designer to choose colors to be used in the design.

Requirements
Must have
• Implicit authority and deep insight. This is a book that says there is depth beyond the cover
Nice to have
• See the brief
Should not have
• the usual arrows, bridges and a shouting style.

```html
<!DOCTYPE html>
<html lang="en">
<head>
<meta charset="utf-8">
<title>Guiding Bold Regeneration — Book Cover</title>
<link href="https://fonts.googleapis.com/css2?family=Bebas+Neue&family=Montserrat:wght@900&family=Poppins:wght@400;500&family=Sacramento&display=swap" rel="stylesheet">
<style>
  :root {
    --stage: #121112;
    --crimson: #a8123f;
    --crimson-deep: #6e0a26;
    --crimson-bright: #b8184a;
    --gold: #e9c15c;
    --gold-soft: #d9ad4a;
    --white: #ffffff;
  }
  html, body {
    margin: 0;
    width: 1200px;
    height: 2400px;
    overflow: hidden;
    background: var(--stage);
  }
  .cover {
    position: absolute;
    left: 0;
    top: 240px;
    width: 1200px;
    height: 1920px;
    display: block;
  }
  .title-main { font-family: "Bebas Neue", "Oswald", sans-serif; fill: var(--white); }
  .subtitle-bold {
    font-family: "Montserrat", sans-serif; font-weight: 900; font-size: 92px;
    fill: var(--white); stroke: var(--crimson-deep); stroke-width: 3; paint-order: stroke;
  }
  .subtitle-script { font-family: "Sacramento", cursive; fill: var(--white); font-size: 96px; }
  .series { font-family: "Poppins", sans-serif; font-weight: 400; font-size: 31px; fill: var(--white); letter-spacing: 9px; }
  .author { font-family: "Poppins", sans-serif; font-weight: 500; font-size: 82px; fill: var(--gold); }
  .author-role { font-family: "Poppins", sans-serif; font-weight: 400; font-size: 27px; fill: var(--white); letter-spacing: 8px; }
</style>
</head>
<body>
<svg class="cover" viewBox="0 0 1200 1920" xmlns="http://www.w3.org/2000/svg">
  <defs>
    <radialGradient id="cover-ground" cx="50%" cy="40%" r="75%">
      <stop offset="0" stop-color="var(--crimson-bright)"/>
      <stop offset="0.6" stop-color="var(--crimson)"/>
      <stop offset="1" stop-color="var(--crimson-deep)"/>
    </radialGradient>
    <radialGradient id="artwork-glow" cx="55%" cy="55%" r="55%">
      <stop offset="0" stop-color="var(--gold)" stop-opacity="0.6"/>
      <stop offset="0.55" stop-color="var(--gold-soft)" stop-opacity="0.28"/>
      <stop offset="1" stop-color="var(--gold-soft)" stop-opacity="0"/>
    </radialGradient>
  </defs>

  <rect class="cover-ground" width="1200" height="1920" fill="url(#cover-ground)"/>

  <rect class="cover-artwork" x="0" y="700" width="1200" height="860" fill="url(#artwork-glow)"
        role="img" aria-label="Gold halftone crossing strokes suggesting interlinked systems"/>

  <g class="book-title">
    <text class="title-main" x="600" y="290" font-size="150" text-anchor="middle" letter-spacing="6">GUIDING</text>
    <text class="title-main" x="600" y="484" font-size="258" text-anchor="middle">BOLD</text>
    <text class="title-main" x="90" y="700" font-size="258" textLength="1020" lengthAdjust="spacingAndGlyphs">REGENERATION</text>
  </g>

  <g class="book-subtitle">
    <text class="subtitle-bold" x="600" y="1109" text-anchor="middle">SHIFT</text>
    <text class="subtitle-script" x="600" y="1185" text-anchor="middle">without</text>
    <text class="subtitle-bold" x="604" y="1281" text-anchor="middle" textLength="440" lengthAdjust="spacingAndGlyphs">BREAKING</text>
  </g>

  <text class="series" x="602" y="1588" text-anchor="middle" textLength="668" lengthAdjust="spacing">THE CHANGE LEADER SERIES</text>
  <text class="author" x="616" y="1700" text-anchor="middle" textLength="814" lengthAdjust="spacingAndGlyphs">HELENA MARWOOD</text>
  <line class="author-rule" x1="200" y1="1731" x2="1006" y2="1731" stroke="var(--gold)" stroke-width="2" opacity="0.8"/>
  <text class="author-role" x="614" y="1777" text-anchor="middle" textLength="816" lengthAdjust="spacing">BUSINESS LEADERSHIP &amp; CHANGE EXPERT</text>
</svg>
</body>
</html>
```